Coastline Premier Retreats Business Card Design

Design a business card for Coastline Premier Retreats. Look at the website for colors and reference. Card should have logo, name, title, office number, mobile number, email, URL and a tagline like, "Luxury Hotel & Resort Email Marketing" (This might change).

https://www.coastlinepremierretreats.example

The rest I will leave up to your imagination.

Contact Information for Business Card

Logo, name, title, office number, mobile number, email, URL and a tagline like, "Luxury Hotel & Resort Email Marketing" (This might change).

```html
<!DOCTYPE html>
<html lang="en">
<head>
<meta charset="utf-8">
<title>Coastline Premier Retreats — Business Card</title>
<link href="https://fonts.googleapis.com/css2?family=Michroma&family=Ubuntu:wght@400;500&display=swap" rel="stylesheet">
<style>
  :root {
    --backdrop: #c9c9c9;
    --brand-orange: #f57200;
    --ink: #111111;
    --paper: #ffffff;
    --stripe: rgba(245, 114, 0, 0.08);
    --stripe-grey: rgba(0, 0, 0, 0.05);
  }
  * { box-sizing: border-box; margin: 0; padding: 0; }
  html, body {
    width: 1200px; height: 900px; overflow: hidden;
    background: var(--backdrop);
  }
  .canvas { position: relative; width: 1200px; height: 900px; }

  .card {
    position: absolute;
    width: 560px; height: 320px;
    border-radius: 26px;
    overflow: hidden;
    box-shadow: 0 6px 16px rgba(0,0,0,0.25);
  }

  /* Front */
  .card-front {
    left: 80px; top: 110px;
    background: var(--brand-orange);
    color: var(--paper);
    display: flex; flex-direction: column; align-items: center; justify-content: center;
  }
  .wordmark {
    font-family: "Michroma", sans-serif;
    font-weight: 400;
    text-align: center;
    line-height: 1.1;
  }
  .wordmark-main { display: block; font-size: 40px; letter-spacing: 2px; }
  .wordmark-sub { display: block; font-size: 15px; letter-spacing: 6px; margin-top: 6px; }
  .card-front .wordmark { color: var(--paper); }
  .tagline {
    margin-top: 52px;
    font-family: "Michroma", sans-serif;
    font-size: 12px; letter-spacing: 1.5px;
    text-transform: uppercase;
  }

  /* Back */
  .card-back {
    left: 560px; top: 470px;
    background: var(--paper);
    color: var(--ink);
  }
  .back-stripes { position: absolute; inset: 0; }
  .card-back .wordmark {
    position: absolute; left: 40px; top: 42px;
    color: var(--ink); text-align: left;
  }
  .card-back .wordmark-main { font-size: 30px; }
  .card-back .wordmark-sub { font-size: 12px; letter-spacing: 5px; }

  .person { position: absolute; left: 40px; top: 160px; }
  .person-name {
    font-family: "Michroma", sans-serif;
    font-size: 17px; letter-spacing: 1px; text-transform: uppercase;
  }
  .person-title {
    font-family: "Ubuntu", sans-serif;
    font-size: 15px; color: var(--brand-orange); margin-top: 4px;
  }
  .phones {
    position: absolute; left: 40px; top: 240px;
    list-style: none;
    font-family: "Ubuntu", sans-serif; font-size: 15px;
  }
  .phones li, .online li { display: flex; align-items: center; gap: 8px; line-height: 24px; }
  .online {
    position: absolute; right: 30px; top: 205px;
    list-style: none; text-align: right;
    font-family: "Ubuntu", sans-serif; font-size: 13px;
  }
  .online li { justify-content: flex-end; }
  .accent { color: var(--brand-orange); }
  .icon { width: 14px; height: 14px; flex: none; }
</style>
</head>
<body>
<main class="canvas">

  <section class="card card-front" aria-label="Business card front">
    <div class="wordmark">
      <span class="wordmark-main">COASTLINE</span>
      <span class="wordmark-sub">PREMIER RETREATS</span>
    </div>
    <p class="tagline">Luxury Hotel &amp; Resort Email Marketing</p>
  </section>

  <section class="card card-back" aria-label="Business card back">
    <svg class="back-stripes" viewBox="0 0 560 320" preserveAspectRatio="none" aria-hidden="true">
      <polygon points="360,0 520,0 400,320 240,320" fill="var(--stripe-grey)"/>
      <polygon points="350,0 356,0 236,320 230,320" fill="var(--stripe)"/>
      <polygon points="528,0 540,0 420,320 408,320" fill="var(--stripe)"/>
    </svg>

    <div class="wordmark">
      <span class="wordmark-main">COASTLINE</span>
      <span class="wordmark-sub">PREMIER RETREATS</span>
    </div>

    <div class="person">
      <h1 class="person-name">Daniel Harper</h1>
      <p class="person-title">Managing Director</p>
    </div>

    <ul class="phones">
      <li>
        <svg class="icon" viewBox="0 0 24 24" aria-label="Office phone"><path d="M6.6 10.8a15 15 0 0 0 6.6 6.6l2.2-2.2a1 1 0 0 1 1-.25 11 11 0 0 0 3.6.6 1 1 0 0 1 1 1V20a1 1 0 0 1-1 1A17 17 0 0 1 3 4a1 1 0 0 1 1-1h3.5a1 1 0 0 1 1 1 11 11 0 0 0 .6 3.6 1 1 0 0 1-.25 1z" fill="var(--brand-orange)"/></svg>
        044-555 010 234
      </li>
      <li>
        <svg class="icon" viewBox="0 0 24 24" aria-label="Mobile phone"><rect x="6" y="2" width="12" height="20" rx="2" fill="none" stroke="var(--brand-orange)" stroke-width="2"/><circle cx="12" cy="18" r="1.2" fill="var(--brand-orange)"/></svg>
        044-555 010 234
      </li>
    </ul>

    <ul class="online">
      <li>
        info@coastlinepremier.example
        <svg class="icon" viewBox="0 0 24 24" aria-label="Email"><rect x="2" y="5" width="20" height="14" fill="var(--brand-orange)"/><path d="M2 5l10 8 10-8" fill="none" stroke="#fff" stroke-width="1.8"/></svg>
      </li>
      <li>
        <span>www.<span class="accent">coastlinepremierretreats</span>.example</span>
        <svg class="icon" viewBox="0 0 24 24" aria-label="Website"><circle cx="12" cy="12" r="9" fill="none" stroke="var(--brand-orange)" stroke-width="2"/><path d="M3 12h18M12 3c3 3 3 15 0 18M12 3c-3 3-3 15 0 18" fill="none" stroke="var(--brand-orange)" stroke-width="1.5"/></svg>
      </li>
    </ul>
  </section>

</main>
</body>
</html>
```